Website for a Psychologist in Private Practice

I need a cool web design for my website: www.drkalvoric.com. I would like it to look professional. Keep all the current content and add: Space for video; radio spots (see Silver Cedar Tunes Logo below for those); Quick Inquiry; Friendora link; 5 star rating on Rivo; a map; reviews from former patients. I am open to suggestions.

Target Market(s)

Those seeking individual and marital counseling.

Industry/Entity Type

Mental Health

Number of Pages Required

1 page

Font styles to use
Sans Serif
Other font styles liked:
• I'm open but no hard to read script

Requirements
Must have
• All the content on my home page with link for video and radio spots. List services and degrees and expertices (pics not necessary).
Nice to have
• A video of me and radio conversations (logo of Silver Cedar Tunes radio attached).
Should not have
• Cartoons, comedy, etc.... I don't need pictures of services (marital, depression, etc...) Just list those.

```html
<!DOCTYPE html>
<html lang="en">
<head>
<meta charset="utf-8">
<title>Dr. Mara L. Kalvoric – Psychologist</title>
<link rel="stylesheet" href="https://fonts.googleapis.com/css2?family=Signika:wght@400;600&family=Arimo:ital,wght@0,400;0,700;1,400;1,700&display=swap">
<style>
:root{
  --blue:#2f86c9;
  --blue-dark:#1f6aa8;
  --teal:#1f5f63;
  --teal-dark:#1b4a4d;
  --band:#3a4344;
  --footer:#1f2324;
  --white:#ffffff;
  --muted:#d7e2e3;
  --ink:#2b2b2b;
  --accent:#e07a2a;
}
*{margin:0;padding:0;box-sizing:border-box}
html,body{width:744px;height:1200px;overflow:hidden}
body{position:relative;font-family:"Arimo",Arial,sans-serif;color:var(--white);
  background:linear-gradient(180deg,#7fb3d8 0%,#b8d6e8 22%,#2fa4b2 40%,#1f7f8f 55%,#8a8a80 72%,#d8c4a8 100%)}
.abs{position:absolute}
.page{position:absolute;left:82px;top:0;width:581px;height:1200px}
.h{font-family:"Signika",sans-serif}

/* header */
.header{left:0;top:0;width:581px;height:58px;background:linear-gradient(180deg,rgba(40,90,130,.75),rgba(70,120,160,.55))}
.site-name{left:8px;top:16px;font-size:25px;font-weight:400}
.license{left:358px;top:34px;font-size:10px}
.call-icon{left:470px;top:22px}
.call-label{left:495px;top:18px;font-size:9.5px}
.call-number{left:495px;top:30px;font-size:14px}

/* nav */
.nav{left:0;top:58px;width:581px;height:28px;background:var(--blue);display:flex;align-items:center;font-size:10px}
.nav a{color:var(--white);text-decoration:none;height:28px;line-height:28px;padding:0 10px;border-right:1px solid rgba(255,255,255,.25)}
.nav a.active{background:#3d95d6;color:var(--ink);font-size:9px}
.follow{left:476px;top:67px;font-size:8px}
.social{left:532px;top:62px;display:flex;gap:6px}
.social span{width:18px;height:18px;border-radius:50%;background:#5aa7de;display:block}

/* hero */
.hero{left:0;top:86px;width:581px;height:272px;background:linear-gradient(180deg,#5d8fb7 0%,#c9c7a8 35%,#f2d98a 55%,#b6c95a 70%,#6f8f2a 100%)}
.hero-kicker{left:64px;top:82px;font-size:16px;color:var(--blue-dark);font-weight:600}
.hero-text{left:65px;top:107px;font-size:14px;line-height:21px;color:var(--ink);width:190px}
.arrow{width:22px;height:22px;background:rgba(40,40,40,.75);top:124px}

/* intro columns */
.intro{left:0;top:358px;width:581px;height:220px;background:linear-gradient(180deg,rgba(28,95,100,.92),rgba(30,100,104,.85))}
.col-title{font-size:14px;line-height:15px}
.rule{height:2px;background:var(--blue)}
.rule::before{content:"";display:block;width:60px;height:3px;background:#152a2b;margin-top:-1px}
.about-text{left:6px;top:70px;width:170px;font-size:8.4px;line-height:13px}
.link{color:var(--white);text-decoration:underline;font-size:9px}
.portrait{left:204px;top:64px;width:64px;height:64px;border-radius:50%;background:radial-gradient(circle at 50% 40%,#e9d6a3,#8a7a6a 70%);border:2px solid var(--white)}
.exp-name{left:276px;top:76px;font-size:14px;line-height:19px}
.exp-list{left:208px;top:134px;font-size:8.6px;line-height:13px;list-style:none}
.exp-list li::before{content:"✓";margin-right:4px}
.quote-box{left:399px;top:70px;width:175px;height:104px;background:#c7d0d0;border:1px solid #a9b3b3;color:#3a3a3a;font-size:8.6px;line-height:13px;padding:8px 8px}
.quote-box .by{text-align:right;font-family:Georgia,serif;font-size:8px;margin-top:2px}
.divider{width:1px;background:rgba(255,255,255,.2)}

/* degrees */
.degrees{left:0;top:578px;width:581px;height:50px;background:rgba(45,52,53,.88)}
.deg-title{left:65px;top:16px;font-size:15px}
.deg-list{font-size:8.6px;line-height:17px}

/* media row */
.sec-title{font-size:14px}
.video{left:6px;top:678px;width:181px;height:137px;border:2px solid var(--blue);background:linear-gradient(160deg,#6f8f7f,#c7b08a 45%,#3e5c7a)}
.play{left:83px;top:58px}
.lead{left:211px;top:681px;font-size:7px;color:#e8e8e8}
.field{left:211px;width:172px;height:18px;background:rgba(60,60,60,.75);font-size:7.5px;color:#cfcfcf;padding:5px 7px}
.submit{left:212px;top:798px;width:68px;height:18px;background:var(--blue);font-size:9px;font-weight:700;text-align:center;line-height:18px}
.radio{left:404px;top:653px;width:163px;height:162px;background:linear-gradient(160deg,#d9346c,#8a4e6a 40%,#3d3b44 75%,#a83a5c)}
.radio-title{left:4px;top:2px;font-size:13px;font-weight:600;color:var(--white)}
.radio-sub{left:6px;top:18px;font-size:9px;font-style:italic;color:#f4d6a0}
.radio-when{left:4px;top:118px;font-size:8px;line-height:10px;font-weight:700}
.radio-inset{left:106px;top:104px;width:53px;height:54px;border:2px solid var(--white);background:linear-gradient(160deg,#5f9cc5,#d8c08a)}

/* reviews */
.reviews{left:0;top:840px;width:581px;height:182px;background:linear-gradient(180deg,rgba(70,70,70,.8),rgba(90,85,80,.65))}
.rev-title{left:0;top:20px;width:581px;text-align:center;font-size:14px}
.rev-photo{left:6px;top:56px;width:72px;height:72px;border-radius:50%;border:2px solid var(--white);background:radial-gradient(circle at 50% 40%,#d6b99a,#2c3a4a 75%)}
.rev-text{left:92px;top:62px;width:474px;font-size:8.2px;line-height:14.6px;font-style:italic}
.rev-by{left:92px;top:131px;font-size:8.2px;font-style:italic;font-weight:700}
.rev-more{left:482px;top:146px;font-size:8.4px}

/* footer */
.footer{left:0;top:1022px;width:581px;height:152px;background:var(--footer)}
.f-title{font-size:9.4px;font-weight:700;padding-bottom:4px;border-bottom:1px dashed #666}
.f-links{list-style:none;font-size:8px;line-height:13.7px}
.f-links li:first-child{color:var(--accent)}
.badge{width:128px;height:48px;border:2px solid #3a6aa8}
.contact{font-size:8px;line-height:11.5px}
.rivo{left:513px;top:36px;width:52px;height:50px;border-radius:8px;background:#c7262e;border:2px solid #e8e8e8}
.share{left:510px;top:98px;width:58px;height:18px;background:#3b5b9a;font-size:8px;line-height:18px;padding-left:20px}
.share::before{content:"";position:absolute;left:5px;top:4px;width:10px;height:10px;background:var(--white)}
.copy{left:0;top:1174px;width:581px;height:26px;background:var(--blue);font-size:8px;text-align:center;line-height:26px}
</style>
</head>
<body>
<div role="img" aria-label="Beach backdrop with sky, sea and sand" class="abs" style="inset:0"></div>
<div class="page">

  <header class="abs header">
    <div class="abs site-name h">Dr. Mara L. Kalvoric</div>
    <div class="abs license h">California # PSY20583</div>
    <svg class="abs call-icon" width="20" height="20" viewBox="0 0 20 20"><circle cx="10" cy="10" r="9" fill="none" stroke="#fff" stroke-width="1.3"/><path d="M7 5c-1 1-1 3 1 6s4 4 5 3l1-1-2-2-1 1c-1 0-3-2-3-3l1-1-1-2z" fill="#fff"/></svg>
    <div class="abs call-label">Call Us Today</div>
    <div class="abs call-number h">555-014-2270</div>
  </header>

  <nav class="abs nav h">
    <a class="active" href="#">Home</a>
    <a href="#">About Me</a>
    <a href="#">Sessions</a>
    <a href="#">Resources</a>
    <a href="#">BIO</a>
    <a href="#">Customer Reviews</a>
    <a href="#" style="border-right:0">Contact Us</a>
  </nav>
  <div class="abs follow h">Follow Us On</div>
  <div class="abs social" aria-label="Friendora and Chirply"><span></span><span></span></div>

  <section class="abs hero">
    <div role="img" aria-label="Man with raised arms in a sunlit meadow" class="abs" style="inset:0"></div>
    <div class="abs hero-kicker h">DO NOT COMPROMISE</div>
    <p class="abs hero-text h">Experience separates good psychologists from others with fewer and more proficient sessions</p>
    <svg class="abs arrow" style="left:4px" viewBox="0 0 22 22"><path d="M13 6l-5 5 5 5" fill="none" stroke="#fff" stroke-width="2"/></svg>
    <svg class="abs arrow" style="left:555px" viewBox="0 0 22 22"><path d="M9 6l5 5-5 5" fill="none" stroke="#fff" stroke-width="2"/></svg>
  </section>

  <section class="abs intro">
    <div class="abs col-title h" style="left:8px;top:18px">About<br>Dr. Mara L. Kalvoric</div>
    <div class="abs rule" style="left:6px;top:56px;width:174px"></div>
    <p class="abs about-text">While I acknowledge the importance of my education, I also appreciate the role my experiences have played in allowing me to relate so well to others. Allow me to share those I feel are most relevant with you.<br>I survived an abusive childhood that my mother &amp; sister unfortunately did not. &amp; it was my grief &amp; desire to become stronger than my past that led me to counseling.....<br><a class="link" href="#">Read More</a></p>
    <div class="abs divider" style="left:190px;top:50px;height:150px"></div>

    <div class="abs col-title h" style="left:206px;top:18px">My<br>Expertise</div>
    <div class="abs rule" style="left:204px;top:56px;width:176px"></div>
    <div role="img" aria-label="Portrait of Dr. Kalvoric" class="abs portrait"></div>
    <div class="abs exp-name h">Dr. Mara L.<br>Kalvoric</div>
    <ul class="abs exp-list h">
      <li>Dating, Marriage,</li>
      <li>Parenting &amp; Professional Relationships</li>
      <li>Depression &amp; Anxiety Issues</li>
      <li>Personality Disorders</li>
      <li>Life Management</li>
    </ul>
    <div class="abs divider" style="left:390px;top:50px;height:150px"></div>

    <div class="abs col-title h" style="left:400px;top:18px">Radio<br>Conversations</div>
    <div class="abs rule" style="left:400px;top:56px;width:174px"></div>
    <div class="abs quote-box"><span style="font-size:14px;color:#777">“</span> Lorem ipsum dolor sit ae onsectetuer adipiscing elit, sed diam nonummy nibh euis tincidunt ut laoreetlore gna aliquam erat olutpat. Ut wisi enim adinim veniam, quis strud xerci tation ullamrper suscipit lobortis sl ut al lorem.<div class="by">Nora Bell</div></div>
    <a class="abs link h" style="left:400px;top:182px" href="#">View All</a>
  </section>

  <section class="abs degrees">
    <div class="abs deg-title h">My Degrees</div>
    <svg class="abs" style="left:148px;top:8px" width="12" height="34" viewBox="0 0 12 34"><path d="M2 1c5 0 5 4 5 8s0 7 4 8c-4 1-4 4-4 8s0 8-5 8" fill="none" stroke="#9aa" stroke-width="1.3"/></svg>
    <div class="abs deg-list h" style="left:170px;top:8px">Doctoral Degree in Clinical Psychology<br>Masters Degree in Counseling Psychology</div>
    <div class="abs deg-list h" style="left:360px;top:8px">Doctoral Internship, Coastal University Medical Center<br>Masters Internship, Ridgeview Clinic</div>
  </section>

  <div class="abs sec-title h" style="left:6px;top:649px">View Video</div>
  <div class="abs rule" style="left:6px;top:668px;width:181px"></div>
  <div role="img" aria-label="Video still of Dr. Kalvoric" class="abs video">
    <svg class="abs play" width="18" height="18" viewBox="0 0 18 18"><circle cx="9" cy="9" r="8" fill="none" stroke="#fff" stroke-width="1.4"/><path d="M7 5l5 4-5 4z" fill="#fff"/></svg>
  </div>

  <div class="abs sec-title h" style="left:211px;top:649px">Quick Inquiry</div>
  <div class="abs rule" style="left:211px;top:668px;width:174px"></div>
  <div class="abs lead">Lorem ipsum dolor sit amet, consectetuer</div>
  <div class="abs field" style="top:696px">Name</div>
  <div class="abs field" style="top:718px">Email</div>
  <div class="abs field" style="top:740px">Phone</div>
  <div class="abs field" style="top:762px;height:30px">Message</div>
  <div class="abs submit">SUBMIT</div>

  <div role="img" aria-label="Silver Cedar Tunes radio show promo with hosts" class="abs radio">
    <div class="abs radio-title h">SILVER CEDAR TUNES</div>
    <div class="abs radio-sub">With Lena and Ivy</div>
    <div class="abs radio-when h"><span style="font-size:11px">SUNDAYS</span><br>4PM PST/7PM EST<br>WAVETALK.FM</div>
    <div class="abs radio-inset"></div>
  </div>

  <section class="abs reviews">
    <div class="abs rev-title h">Reviews From Former Patients</div>
    <div class="abs rule" style="left:196px;top:40px;width:189px;height:1px;background:#ddd"></div>
    <div class="abs" style="left:268px;top:39px;width:46px;height:3px;background:var(--blue)"></div>
    <div role="img" aria-label="Portrait of a former patient" class="abs rev-photo"></div>
    <svg class="abs" style="left:90px;top:58px" width="20" height="14" viewBox="0 0 20 14"><path d="M2 14l3-12h4L6 14zM11 14l3-12h4l-3 12z" fill="#999"/></svg>
    <p class="abs rev-text">&nbsp;&nbsp;&nbsp;&nbsp;&nbsp;&nbsp;&nbsp;Lorem ipsum dolor sit amet, consectetuer adipiscing elit, sed diam nonummy nibh euismod tincidunt ut laoreet dolore magna aliquam erat volutpat. Ut wisi enim ad minim veniam, quis nostrud exerci tation ullamcorper suscipit lobortis nisl ut aliquip commodo consequat. Duis autem vel eum iriure dolor in hendrerit in vulputate velit esse molestie consequat, vel illum dolore eu feugiat nulla facilisis at vero eros et accumsan et iusto odio dignissimaugue duis dolore te feugait nulla facilisi.</p>
    <div class="abs rev-by">.... Lorem Ispum, Manger</div>
    <a class="abs link rev-more" href="#">Read more testimonials</a><span class="abs" style="left:571px;top:145px;font-size:9px">»</span>
  </section>

  <footer class="abs footer">
    <div class="abs f-title" style="left:8px;top:19px;width:74px">Quick Links</div>
    <ul class="abs f-links" style="left:8px;top:41px">
      <li>Home</li><li>About Me</li><li>Sessions</li><li>Resources</li><li>BIO</li><li>Customer Reviews</li><li>Contact Me</li>
    </ul>

    <div class="abs f-title" style="left:130px;top:19px;width:166px">A Portion of All Revenue Is Donated To</div>
    <div class="abs badge" style="left:130px;top:39px;background:var(--white);border-color:#3a6aa8;color:#1f3b7a;font-size:10px;font-weight:700;text-align:center;line-height:44px">Harbor Child Advocates</div>
    <div class="abs badge" style="left:130px;top:93px;background:#8aa63a;border-color:#3a6aa8;font-size:12px;font-weight:700;text-align:center;line-height:44px">Maple Haven</div>

    <div class="abs f-title" style="left:341px;top:19px;width:118px">Contact Details</div>
    <div class="abs contact" style="left:341px;top:43px">A:</div>
    <div class="abs contact" style="left:359px;top:43px">48 Harbor Lane, Suite 210<br>Bayview, CA 90999</div>
    <div class="abs contact" style="left:341px;top:78px">P:&nbsp;&nbsp;&nbsp;&nbsp;&nbsp;555-014-2270</div>
    <div class="abs contact" style="left:341px;top:99px">TF:&nbsp;&nbsp;&nbsp;&nbsp;555-014-2270</div>
    <div class="abs contact" style="left:341px;top:120px">E:&nbsp;&nbsp;&nbsp;&nbsp;&nbsp;mk@drkalvoric.com</div>

    <div class="abs rivo" aria-label="Rivo reviews"></div>
    <div class="abs share">SHARE</div>
  </footer>

  <div class="abs copy">Copyright © 2016 Dr. Mara L. Kalvoric&nbsp; All rights reserved</div>
</div>
</body>
</html>
```